Coffee Bag Design for Tollbury Coffee

We’re excited to invite you to help us bring Tollbury Coffee to life on grocery store shelves with a design that embodies our mission of spreading goodness and creating a lasting impact. Tollbury Coffee represents warmth, positivity, and the power of small actions to create ripples of goodness. Each cup not only offers a rich, gourmet coffee experience but also gives back to the community, with $2 from each bag supporting local food banks.

To reflect this vision, we’d love for the design to feature a dark (greyish) blue as the base color to convey depth and quality, complemented by a vibrant light blue that will catch the eye and add energy. Tan or gold accents could add an elegant touch and a feeling of warmth. We are aiming for a look that feels uplifting and engaging, with simplicity and elegance, yet stands out amid other brands on the shelf.

I am attaching the dimension of the bag.

Other information that needs to be listed:
Ingredients: 100% Arabica Coffee
Net Wt. 12 oz. (340 g)
Roasted and distributed by:
Name
Address
email

Text on the back of the bag:
Tollbury Coffee is crafted with a belief that kindness and positivity can spread, touching countless lives with every sip. This gourmet blend delivers a rich taste experience while giving back, as $2 from each bag sold is donated to local food banks to help those in need. Enjoy the warmth and goodness in each cup, knowing you’re making a difference with every purchase.

Thank you!

```html
<!DOCTYPE html>
<html lang="en">
<head>
<meta charset="utf-8">
<title>Tollbury Coffee – Back Design</title>
<link rel="stylesheet" href="https://fonts.googleapis.com/css2?family=Open+Sans:wght@400;600&family=Questrial&display=swap">
<style>
  :root {
    --bg: #e4e4e6;
    --ink: #1b1b1f;
    --navy-deep: #0f1424;
    --navy: #15223f;
    --navy-mid: #1d325c;
    --navy-light: #2a4a80;
    --gold: #c9a35f;
    --gold-light: #e8cf9c;
    --tan: #e9d6b3;
    --gold-dark: #a07c3c;
  }
  * { box-sizing: border-box; margin: 0; padding: 0; }
  html, body { width: 1200px; height: 933px; overflow: hidden; background: var(--bg); }
  .canvas { position: relative; width: 1200px; height: 933px; background: var(--bg); }

  .view-title {
    position: absolute; top: 28px; left: 0; width: 1200px; text-align: center;
    font-family: "Open Sans", sans-serif; font-size: 28px; color: var(--ink);
  }

  /* round seal label */
  .seal {
    position: absolute; left: 78px; top: 67px; width: 261px; height: 261px; border-radius: 50%;
    background: linear-gradient(180deg, var(--navy-deep) 0%, var(--navy) 100%);
    display: flex; align-items: center; justify-content: center;
  }
  .seal::before {
    content: ""; position: absolute; inset: 18px; border-radius: 50%; border: 1.5px solid var(--gold);
  }
  .brand-name {
    font-family: "Questrial", sans-serif; color: var(--gold); font-weight: 400; text-align: center;
    letter-spacing: 0.02em; line-height: 1.1;
  }
  .seal .brand-name { font-size: 30px; }

  /* flat bag back panel */
  .bag-back {
    position: absolute; left: 620px; top: 82px; width: 440px; height: 820px;
    background: var(--navy); overflow: hidden; border-radius: 6px 6px 0 0;
  }
  .arc-pattern {
    position: absolute; inset: 0;
    background:
      radial-gradient(circle at 20% 30%, var(--navy-light) 0%, transparent 40%),
      radial-gradient(circle at 80% 65%, var(--navy-light) 0%, transparent 42%),
      linear-gradient(180deg, var(--navy-mid) 0%, var(--navy) 100%);
  }
  .center-band {
    position: absolute; left: 150px; top: 0; width: 140px; height: 100%;
    background: var(--navy-deep);
    border-left: 1.5px solid var(--gold); border-right: 1.5px solid var(--gold);
  }
  .band-damask {
    position: absolute; left: 0; top: 330px; width: 100%; height: 120px;
    background: linear-gradient(180deg, var(--navy-mid), var(--navy-deep));
  }
  .gold-stripes {
    position: absolute; left: 40px; top: 0; width: 60px; height: 110px; display: flex;
  }
  .gold-stripes span { flex: 1; }
  .gold-stripes .tan { background: var(--tan); }
  .gold-stripes .gold { background: linear-gradient(90deg, var(--gold-dark), var(--gold)); }

  .pull-tab {
    position: absolute; left: 6px; top: 86px; display: flex; align-items: center; gap: 8px;
    font-family: "Open Sans", sans-serif; font-weight: 600; font-size: 9px; color: var(--tan);
  }
  .pull-tab .tab-mark {
    border: 1px solid var(--tan); border-radius: 3px; padding: 1px 4px; font-size: 9px;
  }
  .pull-tab svg { position: absolute; left: 128px; top: 1px; }

  .bag-seal {
    position: absolute; left: 120px; top: 160px; width: 200px; height: 200px; border-radius: 50%;
    background: linear-gradient(180deg, var(--navy-deep), var(--navy));
    box-shadow: 0 0 0 6px var(--navy-deep);
    display: flex; align-items: center; justify-content: center;
  }
  .bag-seal::before {
    content: ""; position: absolute; inset: 12px; border-radius: 50%; border: 1.5px solid var(--gold);
  }
  .bag-seal .brand-name { font-size: 24px; }

  .story-panel {
    position: absolute; left: 82px; top: 440px; width: 276px; height: 290px;
    background: linear-gradient(180deg, var(--navy-deep), var(--navy));
    border: 3px solid var(--gold); outline: 1px solid var(--gold-light); outline-offset: -7px;
    padding: 52px 20px 20px;
  }
  .story-text {
    font-family: "Questrial", sans-serif; font-size: 11.3px; line-height: 1.42;
    color: var(--tan); text-align: justify; text-align-last: center;
  }
  .flourish {
    position: absolute; left: 50%; width: 56px; height: 12px; margin-left: -28px;
    background: linear-gradient(90deg, transparent, var(--gold), transparent); border-radius: 6px;
  }
  .flourish.top { top: 30px; }
  .flourish.bottom { bottom: 22px; }
</style>
</head>
<body>
<main class="canvas">
  <h1 class="view-title">Back Design</h1>

  <div class="seal">
    <p class="brand-name">Tollbury<br>Coffee</p>
  </div>

  <section class="bag-back" aria-label="Coffee bag back panel">
    <div class="arc-pattern" role="img" aria-label="Pattern of overlapping navy arcs with gold concentric rings"></div>

    <div class="center-band">
      <div class="band-damask" role="img" aria-label="Faint navy damask ornament"></div>
      <div class="gold-stripes"><span class="tan"></span><span class="gold"></span><span class="tan"></span></div>
    </div>

    <div class="pull-tab">
      <span class="tab-mark">TAB</span>
      <span>PULL TAB TO OPEN</span>
      <svg width="290" height="10" viewBox="0 0 290 10" aria-hidden="true">
        <g fill="#e9d6b3">
          <path d="M22 1 L30 5 L22 9Z"/><path d="M46 1 L54 5 L46 9Z"/><path d="M70 1 L78 5 L70 9Z"/>
          <path d="M94 1 L102 5 L94 9Z"/><path d="M118 1 L126 5 L118 9Z"/><path d="M142 1 L150 5 L142 9Z"/>
          <path d="M166 1 L174 5 L166 9Z"/><path d="M190 1 L198 5 L190 9Z"/><path d="M214 1 L222 5 L214 9Z"/>
          <path d="M238 1 L246 5 L238 9Z"/><path d="M262 1 L270 5 L262 9Z"/>
        </g>
      </svg>
    </div>

    <div class="bag-seal">
      <p class="brand-name">Tollbury<br>Coffee</p>
    </div>

    <div class="story-panel">
      <div class="flourish top" role="img" aria-label="Gold scroll ornament"></div>
      <p class="story-text">Tollbury Coffee is crafted with a belief that kindness and positivity can spread, touching countless lives with every sip. This gourmet blend delivers a rich taste experience while giving back, as $2 from each bag sold is donated to local food banks to help those in need. Enjoy the warmth and goodness in each cup, knowing you’re making a difference with every purchase.</p>
      <div class="flourish bottom" role="img" aria-label="Gold scroll ornament"></div>
    </div>
  </section>
</main>
</body>
</html>
```